Professional Website

We are looking for a new website for our Staffing Company. Attached is a document with all the details and pages needed along with some examples of others websites.

We want a professional Look and feel around the same color theme as the attached Amber Compass.

We currently host our site on PageLoom.io. If the winning designer can also add to PageLoom, that is a plus.

```html
<!DOCTYPE html>
<html lang="en">
<head>
<meta charset="utf-8">
<title>CrewPoint Staffing</title>
<link href="https://fonts.googleapis.com/css2?family=Poppins:ital,wght@0,400;0,500;0,600;0,700;1,400&display=swap" rel="stylesheet">
<style>
:root{
  --blue:#2f45c0;
  --blue-bright:#2b42c8;
  --ink:#1d1d1f;
  --dark:#2d2d2f;
  --footer:#1b1a1c;
  --white:#ffffff;
  --rule:#3c3b3e;
}
*{margin:0;padding:0;box-sizing:border-box}
html,body{width:1083px;height:1200px;overflow:hidden;background:var(--white);font-family:'Poppins',sans-serif;color:var(--ink)}
.page{position:relative;width:1083px;height:1200px}

.site-header{position:absolute;top:0;left:0;width:1083px;height:100px;background:var(--white)}
.brand{position:absolute;left:90px;top:14px;display:flex;align-items:center;gap:10px}
.brand-mark{width:18px;height:18px;background:var(--blue)}
.brand-name{font-weight:700;font-size:46px;line-height:1;color:var(--blue);letter-spacing:-1px}
.logins{position:absolute;top:9px;left:449px;display:flex;gap:5px}
.login-btn{width:134px;height:38px;border:1.5px solid var(--blue);border-radius:3px;color:var(--blue);font-size:12px;font-weight:500;display:flex;align-items:center;justify-content:center}
.hotline{position:absolute;left:868px;top:11px;display:flex;gap:6px;color:var(--blue);font-size:13px;line-height:16px}
.hotline strong{font-weight:600}
.main-nav{position:absolute;top:66px;left:447px;width:546px;display:flex;justify-content:space-between;font-size:13px;font-weight:500;line-height:16px}
.main-nav .active{color:var(--blue)}

.hero{position:absolute;top:100px;left:0;width:1083px;height:567px;display:flex}
.hero-dark{width:542px;height:100%;background:var(--dark)}
.hero-blue{width:541px;height:100%;background:var(--blue)}
.person{position:absolute;bottom:0}
.person-left{left:0;width:285px;height:530px;background:linear-gradient(180deg,#4a4442 0%,#232325 60%,#1b1b1d 100%);border-radius:140px 140px 0 0}
.person-right{left:810px;width:273px;height:530px;background:linear-gradient(180deg,#3b2a25 0%,#253a8e 55%,#1e2f78 100%);border-radius:140px 140px 0 0}
.hero-copy{position:absolute;left:240px;top:152px;width:603px;text-align:center;color:var(--white)}
.hero-copy h1{font-size:30.5px;font-weight:700;line-height:40px;text-transform:uppercase}
.hero-copy p{margin-top:12px;font-size:14px;line-height:31.5px;text-align:justify;text-align-last:center}
.hero-actions{position:absolute;top:360px;left:341px;display:flex}
.cta{width:200px;height:49px;display:flex;align-items:center;justify-content:center;color:var(--white);font-size:14px;font-weight:600}
.cta-job{background:var(--blue-bright)}
.cta-hire{background:var(--dark)}

.mission{position:absolute;top:724px;left:90px;width:903px;text-align:center;font-style:italic;font-size:19px;line-height:37.3px}

.site-footer{position:absolute;top:970px;left:0;width:1083px;height:230px;background:var(--footer);color:var(--white)}
.footer-brand{position:absolute;left:90px;top:38px;display:flex;align-items:center;gap:12px}
.footer-brand .brand-mark{background:var(--white);width:22px;height:22px}
.footer-brand .brand-name{color:var(--white);font-size:58px}
.areas{position:absolute;left:554px;top:42px}
.areas h3{font-size:15.5px;font-weight:600;margin-bottom:6px}
.areas li{list-style:none;font-size:13.5px;line-height:23px}
.footer-hotline{position:absolute;left:758px;top:45px;display:flex;gap:12px}
.phone-badge{width:51px;height:51px;border-radius:50%;background:var(--blue);display:flex;align-items:center;justify-content:center}
.footer-hotline .label{font-size:16px;font-weight:600;line-height:22px;margin-top:2px}
.footer-hotline .number{font-size:22px;line-height:28px}
.footer-rule{position:absolute;left:90px;top:177px;width:903px;height:1px;background:var(--rule)}
.copyright{position:absolute;top:193px;left:0;width:1083px;text-align:center;font-size:14.5px}
</style>
</head>
<body>
<div class="page">
  <header class="site-header">
    <div class="brand"><span class="brand-mark"></span><span class="brand-name">CrewPoint</span></div>
    <div class="logins">
      <div class="login-btn">Employee Login</div>
      <div class="login-btn">FastPay Card Login</div>
      <div class="login-btn">North Bank Login</div>
    </div>
    <div class="hotline">
      <svg width="24" height="24" viewBox="0 0 24 24" fill="none" stroke="#2f45c0" stroke-width="1.4"><path d="M5 3l3 0 2 5-2 1.5c1 2.5 3 4.5 5.5 5.5L15 13l5 2v3c0 1-1 2-2 2C10 20 4 14 3 6c0-1.5 1-3 2-3z"/><path d="M14 3a7 7 0 017 7M14 6.5a3.5 3.5 0 013.5 3.5"/></svg>
      <div>Hotline #<br><strong>555-014-2200</strong></div>
    </div>
    <nav class="main-nav">
      <span class="active">HOME</span><span>|</span><span>ABOUT</span><span>|</span><span>JOB &#8964;</span><span>|</span><span>OFFICE INFO</span><span>|</span><span>CONTACT US</span>
    </nav>
  </header>

  <section class="hero">
    <div class="hero-dark"></div>
    <div class="hero-blue"></div>
    <div class="person person-left" role="img" aria-label="Portrait of a businessman in a dark suit with arms crossed"></div>
    <div class="person person-right" role="img" aria-label="Portrait of a smiling businesswoman in a navy blazer with arms crossed"></div>
    <div class="hero-copy">
      <h1>Recruiting agency for temporary<br>and direct hire employees</h1>
      <p>Are you tired of the average temporary staffing agency that sends unqualified warm bodies? We’re the first and only recruiting agency specializing in long-term temporary and direct hire staffing.</p>
    </div>
    <div class="hero-actions">
      <div class="cta cta-job">I’m looking for a Job</div>
      <div class="cta cta-hire">I need Employees</div>
    </div>
  </section>

  <p class="mission">Greatest part of our daily job is that we are constantly bringing people together. Our Clients come to us in search of the perfect candidate and the job hunters approach us when they are in need of a job or looking for their next exciting role. Being able to work with and connect the two is incredibly satisfying. Not to mention that in today's current job market, employers are fighting for the top talent. This makes our employees and partners grateful for the help in finding it!</p>

  <footer class="site-footer">
    <div class="footer-brand"><span class="brand-mark"></span><span class="brand-name">CrewPoint</span></div>
    <div class="areas">
      <h3>Areas we service</h3>
      <ul><li>Cedar Ridge</li><li>Maple Falls</li><li>Stonebrook</li></ul>
    </div>
    <div class="footer-hotline">
      <div class="phone-badge">
        <svg width="22" height="22" viewBox="0 0 24 24" fill="none" stroke="#ffffff" stroke-width="2"><path d="M5 3l3 0 2 5-2 1.5c1 2.5 3 4.5 5.5 5.5L15 13l5 2v3c0 1-1 2-2 2C10 20 4 14 3 6c0-1.5 1-3 2-3z"/><path d="M14 3a7 7 0 017 7M14 6.5a3.5 3.5 0 013.5 3.5"/></svg>
      </div>
      <div><div class="label">Hotline</div><div class="number"># 555-014-2200</div></div>
    </div>
    <div class="footer-rule"></div>
    <div class="copyright">©Copyright ©2022 crewpoint staffing. All Rights Reserved.</div>
  </footer>
</div>
</body>
</html>
```